Dentistry Office

We want a new design for a Dentist's office website.

The theme is: "We provide high quality, state-of-the-art, dental care in a comfortable, caring environment."

The site currently has a menu on the left of the page with about 40 items on it. There is a great deal of textual content on each page, plus several illustrations.

We want to do this using CSS, so we need specifications in the CSS for all possible elements. The CSS needs to be named in a logical manner for easy use.

Every dentist on the planet seems to use lots of Flash. We don't want to because it is so distracting. We are looking for an elegant solution targeting 24-55 age group, but not excluding anyone.

The following (from another dentist's site) can give you a taste of what we want to communicate on the site:

"After 20 years of teaching dentists how to refine their technique and many years of writing textbooks, I currently devote my time to my office and the hands-on practice of dentistry. I'd like to welcome you personally to my dental practice, and I invite you to meet my highly experienced team of professionals.

"We have offered complete dental care of the highest quality since 1978. We provide Preventive Services, Tooth Whitening and Cosmetic Dentistry for a beautiful smile, Endodontics (root canal treatment) to treat painful teeth, Sedation Dentistry so you can relax, and Dental Implants to restore what is missing. We offer total care.

"Our approach to your health is simple: We use our education, experience and dedication to provide every patient with superior dental care.

"This passion for excellence is not just a goal, but a standard every member of our team holds.

"We also pride ourselves with our state of the art procedures, training and technology. This includes creating a beautiful smile using techniques that preserve as much of the original tooth as possible.

"Our abilities are renowned throughout the dental profession and I hope if you have any questions you will contact us by an e-mail note, by phone or just by dropping by."

Keep in mind the screen shape and dimensions. Your design needs to work in the normal screen proportions, regardless of how it looks when you post it here. Scrolling is OK, but the first impression needs to work.
Updates

Keep in mind that there will be about 250 words, or more, on each page.

Competitors web sites:

http://www.brindlecovedentist.example/

http://www.brindlecovedentalcare.example/

http://www.grinsbymarlowvaledental.example/

http://www.tenbyfamilydentalcare.example/

http://www.quelmardental.example/

http://www.dovrinadental.example/

We need to compete with these.

Target Market(s)

Generally adults seeking the most experienced and comfortable-to-be-with dentist.

Industry/Entity Type

Training

Requirements
Must have
• Must stand apart from other dentists.
• Must be elegant.
• Must have a horizontal menu structure across all columns, NOT a vertical that requires scrolling, no popout, pop down, etc. menus.
• We are looking for something special.
• Do not waste your time or ours putting up templates and things you have used before.
• Personally, I do not see how someone outside the US can understand the northern California dental market. But you are welcome to try.
Should not have
• Flash or graphics that move
• The look of a template
• Folksy fonts
• Looks like you used it 20 times before

```html
<!DOCTYPE html>
<html lang="en">
<head>
<meta charset="utf-8">
<title>Peter Lindqvist, DDS, FAGD — Santa Rosa Dentist</title>
<link href="https://fonts.googleapis.com/css2?family=Tinos:ital,wght@0,400;0,700;1,400;1,700&family=Noto+Sans:wght@400;700&display=swap" rel="stylesheet">
<style>
:root{
  --ink:#2a2a2a;
  --text:#3b3b3b;
  --muted:#666;
  --nav:#1e1e1e;
  --nav-line:#555;
  --hero-a:#7f93a6;
  --hero-b:#b8c6d3;
  --menu-bg:#e7eaee;
  --menu-line:#9aa4ae;
  --box:#f1f1f1;
  --box-line:#dcdcdc;
  --rule:#c9c9c9;
  --footer:#d9dcdf;
  --white:#fff;
  --serif:'Tinos', Georgia, serif;
  --sans:'Noto Sans', Verdana, sans-serif;
}
*{box-sizing:border-box;margin:0;padding:0}
html,body{width:1200px;height:2590px;overflow:hidden;background:var(--white)}
body{font-family:var(--sans);color:var(--text);font-size:13px;line-height:1.4;position:relative}

.site-header{height:105px;display:flex;justify-content:space-between;padding:14px 30px 0 34px}
.practice-name{font-family:var(--serif);font-size:34px;color:var(--ink);line-height:1.05}
.practice-name small{display:block;font-size:20px;color:var(--muted);padding-left:160px;margin-top:4px}
.practice-address{font-family:var(--serif);font-size:15px;line-height:1.25;color:var(--ink);text-align:left}
.practice-address strong{font-size:17px;font-weight:400}

.main-nav{height:40px;background:var(--nav);display:flex;align-items:center;padding-left:40px}
.main-nav a{color:var(--white);font-family:var(--serif);font-size:16px;text-decoration:none;padding:0 34px;border-right:1px solid var(--nav-line);line-height:20px}
.main-nav a:first-child{padding-left:32px}
.main-nav a:last-child{border-right:none}

.hero{height:275px;position:relative;background:linear-gradient(100deg,var(--hero-a) 0%,var(--hero-b) 60%,#dfe6ec 100%)}
.hero-title{position:absolute;left:60px;top:90px;width:760px;font-family:var(--serif);font-size:26px;line-height:1.25;color:var(--white)}
.hero-photo{position:absolute;right:0;top:0;width:330px;height:275px;background:linear-gradient(90deg,rgba(223,230,236,0),#ecd9d3 40%,#e9c7c8 100%)}

.service-menu{height:230px;background:var(--menu-bg);display:flex;padding:12px 0 0 34px;border-bottom:1px solid var(--rule)}
.menu-group{width:236px}
.menu-group h4{font-family:var(--serif);font-size:19px;color:var(--ink);font-weight:700;border-bottom:1px solid var(--menu-line);margin-right:26px;padding-bottom:2px;margin-bottom:4px}
.menu-group ul{list-style:none}
.menu-group li{font-size:12.5px;line-height:16.5px;color:var(--text)}
.menu-group li::before{content:"› ";color:var(--muted)}

.content{position:absolute;top:700px;left:34px;width:772px}
.page-title{font-family:var(--serif);font-size:26px;color:var(--ink);font-weight:400}
.intro p{margin-top:8px}
.section-title{font-family:var(--serif);font-size:21px;color:var(--ink);margin:14px 0 6px}
.challenge{background:var(--box);border-top:1px solid var(--box-line);position:relative;padding:10px 200px 10px 10px;margin-bottom:14px}
.challenge.has-photo{min-height:150px}
.challenge h3{font-family:var(--serif);font-size:21px;font-weight:400;color:var(--ink);margin-bottom:6px}
.challenge p{margin-bottom:10px}
.challenge p:last-of-type{margin-bottom:0}
.challenge .lead{font-weight:700}
.challenge-photo{position:absolute;right:6px;top:26px;width:170px;height:118px}

.sidebar{position:absolute;top:718px;left:885px;width:280px}
.office-photo{width:255px;height:230px;background:linear-gradient(160deg,#6f7f55,#a98c6b 55%,#4f5d3b);border:1px solid var(--rule)}
.map-box{margin-top:14px;border:1px solid var(--rule);padding:8px 12px;height:418px}
.map-box h3,.hours h3{font-family:var(--serif);font-size:21px;font-weight:400;color:var(--ink);text-align:center}
.map-area{width:250px;height:340px;margin:6px auto 0;background:linear-gradient(135deg,#f4f4f4,#dcdcdc);border:1px solid #bbb}
.map-box a{display:block;text-align:center;font-size:12px;color:var(--ink);margin-top:6px;text-decoration:underline}
.hours{margin-top:30px;border:1px solid var(--rule);padding:8px 14px;height:272px}
.hours p{font-size:13px;margin:6px 0}
.hours li{list-style:none;font-size:13.5px;line-height:22px}
.hours li b{font-style:italic}

.site-footer{position:absolute;left:0;top:2405px;width:1200px;height:185px;background:var(--footer);border-top:3px solid var(--rule);padding:20px 34px}
.footer-meta{font-size:12.5px;line-height:17px}
.footer-meta p:first-child{margin-bottom:14px}
.dental-links{position:absolute;right:30px;top:18px;width:540px;height:150px;background:var(--white);border:1px solid var(--rule);padding:6px 10px}
.dental-links h4{font-size:13px;font-weight:400;color:var(--ink)}
.link-cols{display:flex;gap:20px;margin-top:4px}
.link-col{width:150px}
.badge{height:36px;width:110px;background:#b9c0c7;margin-bottom:4px}
.link-col li{list-style:none;font-size:10.5px;line-height:13px}
</style>
</head>
<body>

<header class="site-header">
  <div class="practice-name">Peter Lindqvist, DDS, FAGD<small>Santa Rosa Dentist</small></div>
  <address class="practice-address"><strong>Peter Lindqvist, DDS, FAGD</strong><br>2240 Larkfield Way, Ste B<br>Santa Rosa, CA 95403<br>707-555-0142</address>
</header>

<nav class="main-nav">
  <a>Home</a><a>Why We Are Different?</a><a>Technologies We Offer</a><a>Meet Dr. Lindqvist</a><a>Our Staff</a><a>Contact Us / Links</a>
</nav>

<section class="hero">
  <h1 class="hero-title">Santa Rosa Dentist - Peter Lindqvist, DDS, Providing Cosmetic Dentistry Excellence to Patients in Santa Rosa, Sonoma County and the San Francisco Bay Area.</h1>
  <div class="hero-photo" role="img" aria-label="Smiling patient holding a pink flower"></div>
</section>

<nav class="service-menu">
  <div class="menu-group"><h4>Education</h4><ul><li>Emergency Dental Care</li><li>Your Mouth</li><li>Your Tooth</li><li>Cracked Tooth?</li><li>Missing a Tooth?</li><li>Sensitive Teeth</li><li>Dry Mouth</li><li>Tooth Grinding</li><li>Sleep Dentistry</li><li>Videos</li></ul></div>
  <div class="menu-group"><h4>Preventative</h4><ul><li>What is Preventive Care?</li><li>Taking Care of Your Teeth</li><li>Eating Right</li><li>Dental Check-Ups</li><li>Sealants</li><li>Periodontal Disease</li><li>Kicking the Habit</li><li>Night Guards</li><li>Dental X-Rays</li><li>Antibiotics with Treatment</li></ul></div>
  <div class="menu-group"><h4>Cosmetics</h4><ul><li>Cosmetic Dentistry</li><li>Bleaching and Whitening</li><li>Cosmetic Bonding</li><li>Esthetic Veneers</li><li>Tooth Shaping</li></ul></div>
  <div class="menu-group"><h4>Restorations</h4><ul><li>Crowns/Caps: Each Step</li><li>CMBRs</li><li>Porcelain Bridges</li><li>Bonded Dental Bridges</li><li>Gold Restorations</li><li>Implants</li><li>Treating Cracked Teeth</li><li>Periodontal (gum) Treatment</li></ul></div>
  <div class="menu-group"><h4>Visiting our office</h4><ul><li>Where to Stay</li><li>First Visit / Map</li><li>Financial Policy</li><li>Dental Insurance</li></ul></div>
</nav>

<main class="content">
  <h2 class="page-title">Welcome to Our Website</h2>
  <div class="intro">
    <p>In Santa Rosa, when you're a patient of Dr. Lindqvist, you can be confident that you're receiving care from the most experienced, knowledgeable, and skilled cosmetic dentist in Sonoma County.</p>
    <p>Dr. Lindqvist is an award-winning leader in restorative dentistry and a genial professional. His humor, dedication, and talent ensure you a pleasant experience and superb, long-lasting results.</p>
  </div>
  <h2 class="section-title">What Are Your Dental Challenges?</h2>

  <div class="challenges">
    <article class="challenge has-photo">
      <h3>Toothache?</h3>
      <p>Toothaches are about as bad a pain as you can experience. We know and we sympathize. That's why we make every effort to bring you immediate relief by keeping room in our schedule for this type of emergency.</p>
      <p>Give us a call right now at (707) 555-0142 and we'll get you in TODAY!</p>
      <p class="lead">Toothaches can largely be avoided with proper preventive care.</p>
      <div class="challenge-photo" role="img" aria-label="Man holding his jaw in pain" style="background:linear-gradient(135deg,#3a3a3a,#9a9a9a)"></div>
    </article>
    <article class="challenge has-photo">
      <h3>Dental Check-Ups</h3>
      <p>Dental check-ups and removal of plaque and tartar from your teeth are the cornerstone of good dental health. Not only can you prevent most toothaches, you may be surprised at how much better and more energetic your entire body feels. Low-grade infections may be lurking in your gums and sapping your energy. See more information by visiting our pages under Preventative in the left side bar.</p>
      <p>Dental check-ups should become a routine habit and be done at least every six months. You will also save a lot of money by avoiding the cost of major dental work incurred by neglect of your dental health.</p>
      <p>Give us a call right now at <strong>(707) 555-0142</strong> and make an appointment!</p>
      <div class="challenge-photo" role="img" aria-label="Dentist examining a patient" style="background:linear-gradient(135deg,#c9b39a,#e6ecf1)"></div>
    </article>
    <article class="challenge has-photo">
      <h3>Deathly Fear of Dentist?</h3>
      <p>With today's technologies that is no longer an excuse. You can be blissfully asleep while even major procedures are performed. When you wake up, everything is done and you're on your way. We specialize in sedation dentistry, also known as sleep dentistry, and you can learn more by clicking here. (make clicking here a text link to this page: <strong>http://www.lindqvistdental.example/sleep-dentistry.htm</strong></p>
      <p>Give us a call right now at <strong>(707) 555-0142</strong> and make an appointment!</p>
      <div class="challenge-photo" role="img" aria-label="Nervous man biting his nails" style="background:linear-gradient(135deg,#d8c3aa,#f2f2f2)"></div>
    </article>
    <article class="challenge has-photo">
      <h3>Cosmetic Dentistry</h3>
      <p class="lead">Who do you think will get the date or have the winning job interview?</p>
      <p>When face-to-face with an important person, nothing speaks louder than a winning smile. Crooked teeth, gaps in your teeth or stains are NOT part of a winning smile. Learn more about our cosmetic dentistry services by clicking on the pages under Cosmetics in the left sidebar.</p>
      <p class="lead">Are you ready to stack the odds in your favor?</p>
      <p>Give us a call right now at <strong>(707) 555-0142</strong> and make an appointment!</p>
      <div class="challenge-photo" role="img" aria-label="Before and after smile comparison" style="background:linear-gradient(90deg,#b08a6a 50%,#e9e4dc 50%)"></div>
    </article>
    <article class="challenge has-photo">
      <h3>Concerned about Mercury Amalgams and Radiation Exposure?</h3>
      <p>You are wise to take your health into your own hands and question the things that have been accepted by patients without question in the past. Amalgams, the so-called silver fillings, are a technology that is over 100 years old. It was cheap, and it lasted a long time. Because of the toxic mercury content of amalgams, we no longer use this technology. We use only the finest, modern tooth-colored bonding materials available.</p>
      <div class="challenge-photo" role="img" aria-label="Teeth with silver amalgam fillings" style="background:linear-gradient(135deg,#8c6b5a,#d9c6b8)"></div>
    </article>
    <article class="challenge has-photo">
      <h3>Removal of Silver Fillings</h3>
      <p>Many of our patients take preventive action and have their old amalgam fillings removed and replaced with modern materials. We take great care when removing the old material so that the toxic mercury contained in amalgams does not come into contact with the inside of your mouth.</p>
      <div class="challenge-photo" role="img" aria-label="Dental x-ray of molars" style="background:linear-gradient(135deg,#2b2b2b,#9b9b9b)"></div>
    </article>
    <article class="challenge">
      <h3>Radiation-Free Diagnostics</h3>
      <p>X-ray-- free decay diagnostics does exist, and we offer this latest technology. It's called Optical Transillumination. Ultra high-speed radiographs for near zero X-ray exposure are also available. Click here to learn more about all of the latest technologies available at Dr. Lindqvist.</p>
      <p>click here: <strong>http://www.lindqvistdental.example/technology.htm</strong></p>
      <p>If you are a health-conscious patient, give us a call right now at <strong>(707) 555-0142</strong> and make an appointment!</p>
    </article>
    <article class="challenge">
      <h3>Free Dental Consultations</h3>
      <p>Let us take a look at your dental challenges, and we will prepare a treatment plan at no cost or obligation to you.</p>
      <p class="lead">Give us a call right now at (707) 555-0142 and make an appointment for a free dental consultation</p>
    </article>
  </div>
</main>

<aside class="sidebar">
  <div class="office-photo" role="img" aria-label="Dental office building among trees"></div>
  <div class="map-box">
    <h3>Santa Rosa Map:</h3>
    <div class="map-area" role="img" aria-label="Street map of Santa Rosa showing the office location"></div>
    <a>Click for Large View</a>
  </div>
  <div class="hours">
    <h3>Office Timing</h3>
    <p>Our usual office hours are:</p>
    <ul>
      <li><b>Monday</b> 9 am to 6 pm</li>
      <li><b>Tuesday</b> 9 am to 5 pm</li>
      <li><b>Wednesday</b> 9 am to 5 pm</li>
      <li><b>Thursday</b> 9 am to 5 pm</li>
      <li><b>Friday</b> 7:30 am to 5 pm</li>
    </ul>
  </div>
</aside>

<footer class="site-footer">
  <div class="footer-meta">
    <p>Copyright © 2010 lindqvistdental.example. All Rights Reserved.</p>
    <p>Office Phone: (707) 555-0142<br>Office Fax: (707) 555-0187<br>email Dr. Lindqvist at: dr@lindqvistdental.example</p>
  </div>
  <div class="dental-links">
    <h4>Dental Links:</h4>
    <div class="link-cols">
      <div class="link-col"><div class="badge"></div><ul><li>Emergency Dental Help</li><li>Oral Health Videos</li><li>Oral Health Topics</li><li>Dental Minute News</li></ul></div>
      <div class="link-col"><div class="badge"></div><ul><li>Dental Emergencies</li><li>Dental Health</li><li>Dental Insurance</li><li>Kids Corner</li><li>Dental Terminology</li></ul></div>
      <div class="link-col"><div class="badge"></div><ul><li>Course Outlines</li><li>Upcoming Courses</li><li>Web Links</li><li>Dr. Lindqvist CV</li><li>Study Club Store</li></ul></div>
    </div>
  </div>
</footer>

</body>
</html>
```